Website improvements and Adding Functionalities at https://mervo.site/tarnovex

1.Search functionality
2.Payment process functionality
3. Application configuration
4. Registration functionality activation
5. Chat functionality
6.Language switching functionality (Portuguese & French)
7.Bespoke interactive modules
8. Automated web scraping and data synchronisation mechanisms
9. News Page
10.Webinar facilities
11. Basic SEO optimisation
12. Speed and performance optimisation
13. Security configuration
14. Google Analytics integration
15. Cross-browser and mobile testing
16. Website deployment and launch support

Target Market(s)

My target markets are companies, investors, suppliers and professionals with an interest in the Mozambican oil and gas sector

Industry/Entity Type

Oil and Gas

Coding

Coded - Design and coding required

Number of Pages Required

1 page

Requirements
Must have
• Improve the existing page at https://mervo.site/tarnovex and add the following features to it: 1. Search functionality 2. Payment process functionality 3. Application configuration 4. Activation of registration functionality 5. Chat functionality 6. Language switching functionality (Portuguese & French) 7. Bespoke interactive modules 8. Automated web scraping and data synchronisation mechanisms 9. News Page

```html
<!DOCTYPE html>
<html lang="en">
<head>
<meta charset="utf-8">
<title>Tarnovex – Mozambique Oil &amp; Gas Intelligence</title>
<link href="https://fonts.googleapis.com/css2?family=Oswald:wght@500;600;700&family=Roboto:wght@400;500;700&display=swap" rel="stylesheet">
<style>
:root{
  --navy:#16112f;
  --navy-2:#1d1740;
  --orange:#e0531d;
  --orange-2:#f4a12f;
  --cream:#f3f0ea;
  --ink:#1b1838;
  --text:#3b3b48;
  --grey:#e9e9ec;
  --white:#ffffff;
}
*{margin:0;padding:0;box-sizing:border-box}
html,body{width:1200px;height:4695px;overflow:hidden}
body{font-family:"Roboto",Arial,sans-serif;color:var(--text);background:var(--white);position:relative}
.abs{position:absolute}
.display{font-family:"Oswald",Impact,sans-serif;font-weight:700;text-transform:uppercase;color:var(--ink);letter-spacing:-.5px}
.accent{color:var(--orange)}
.rule{position:absolute;width:58px;height:4px;background:linear-gradient(90deg,var(--orange),var(--orange-2))}
.btn{position:absolute;display:flex;align-items:center;justify-content:center;gap:8px;font-family:"Roboto",sans-serif;font-weight:700;font-size:14px;color:#fff;text-transform:uppercase;background:linear-gradient(90deg,var(--orange),#f07a22);height:42px;letter-spacing:.2px}
.btn svg{width:9px;height:12px}

/* header */
.site-header{position:absolute;left:0;top:0;width:1200px;height:90px;background:var(--cream)}
.brand{position:absolute;left:0;top:0;width:270px;height:130px;background:var(--cream);clip-path:polygon(0 0,100% 0,90% 100%,0 100%);z-index:3;display:flex;align-items:center;justify-content:center;gap:10px}
.brand-mark{width:22px;height:22px;background:var(--orange)}
.brand-name{font-family:"Roboto",sans-serif;font-weight:700;font-size:22px;color:var(--ink);letter-spacing:1px}
.search{position:absolute;left:442px;top:13px;width:268px;height:30px;border:1px solid #bbb;background:#fff;font-size:12px;color:#555;padding:7px 10px}
.search-btn{position:absolute;right:2px;top:2px;width:24px;height:24px;background:#d42b1e}
.lang{position:absolute;left:746px;top:14px;display:flex;align-items:center;gap:6px;font-size:12px;font-weight:700;color:var(--ink)}
.lang-flag{width:30px;height:30px;border-radius:50%;background:linear-gradient(#2c3f87 0 100%)}
.mail{position:absolute;left:848px;top:0;width:277px;height:50px;background:var(--navy);color:#fff;font-size:12px;font-weight:700;display:flex;align-items:center;gap:8px;padding-left:18px}
.mail span{color:var(--orange);font-weight:500}
.nav{position:absolute;left:292px;top:62px;display:flex;gap:25px;font-size:11.5px;font-weight:700;color:var(--ink);text-transform:uppercase}
.nav .active{color:var(--orange)}

/* hero */
.hero{position:absolute;left:0;top:90px;width:1200px;height:703px;background:linear-gradient(100deg,#1c2540 0%,#2b3a5c 45%,#5d6f8d 70%,#3a4660 100%)}
.hero-worker{position:absolute;left:700px;top:130px;width:500px;height:573px;background:radial-gradient(ellipse at 60% 55%,#e8632a 0%,#a44a2c 35%,rgba(40,50,75,0) 70%)}
.hero-eyebrow{position:absolute;left:93px;top:172px;font-family:"Oswald",sans-serif;font-weight:600;font-size:22px;color:var(--orange)}
.hero-title{position:absolute;left:93px;top:212px;border-left:4px solid var(--orange-2);padding-left:20px;font-family:"Oswald",sans-serif;font-weight:700;font-size:54px;line-height:64px;color:#fff}
.hero-arrow{position:absolute;top:577px;width:34px;height:34px;border-radius:50%;background:#fff;display:flex;align-items:center;justify-content:center}

/* unique */
.unique{position:absolute;left:0;top:793px;width:1200px;height:641px;background:var(--navy)}
.unique h2{position:absolute;left:0;width:1200px;top:135px;text-align:center;font-size:46px;color:#fff}
.step{position:absolute;top:250px;width:270px;text-align:center;color:#fff}
.step-ring{margin:0 auto;width:140px;height:140px;border-radius:50%;border:2px solid var(--orange);position:relative;display:flex;align-items:center;justify-content:center}
.step-core{width:116px;height:116px;border-radius:50%;background:#fff;display:flex;align-items:center;justify-content:center}
.step-num{position:absolute;top:-16px;left:50%;margin-left:-17px;width:34px;height:34px;border-radius:50%;background:var(--orange);color:#fff;font-size:13px;display:flex;align-items:center;justify-content:center}
.step h3{margin-top:22px;font-size:18px;font-weight:700;line-height:27px;text-transform:uppercase}
.step p{margin-top:6px;font-size:14px;line-height:24px;color:#e6e6ee}

/* about */
.about{position:absolute;left:0;top:1434px;width:1200px;height:671px;background:#fff}
.about-photo{position:absolute;left:144px;top:114px;width:427px;height:429px;background:linear-gradient(180deg,#7b6aa8 0%,#c98aa6 35%,#3a3550 65%,#1b2236 100%)}
.about-text{position:absolute;left:607px;top:185px;width:448px;font-size:16.5px;line-height:28px;text-align:justify}
.about h2{position:absolute;left:607px;top:120px;font-size:46px}

/* access */
.access{position:absolute;left:0;top:2105px;width:1200px;height:1041px;background:linear-gradient(135deg,#eeeef0,#dcdce0 50%,#efeff1)}
.access h2{position:absolute;left:0;width:1200px;top:125px;text-align:center;font-size:46px}
.grid{position:absolute;left:144px;top:215px;width:912px;display:grid;grid-template-columns:repeat(3,1fr);background:#fff}
.cell{height:329px;border-right:1px solid #333;border-bottom:1px solid #333;text-align:center;padding:46px 30px 0}
.cell:nth-child(3n){border-right:none}
.cell:nth-child(n+4){border-bottom:none}
.cell svg{width:84px;height:84px}
.cell h3{margin-top:22px;font-size:18px;font-weight:700;line-height:27px;color:var(--ink);text-transform:uppercase}
.cell p{margin-top:10px;font-size:14px;line-height:24px}
.cell.featured{background:linear-gradient(90deg,#d9481d,#f6a835)}
.cell.featured h3,.cell.featured p{color:#fff}

/* how */
.how{position:absolute;left:0;top:3146px;width:1200px;height:537px;background:var(--navy)}
.how-photo{position:absolute;left:630px;top:0;width:570px;height:537px;clip-path:polygon(8% 0,100% 0,100% 100%,0 100%);background:linear-gradient(110deg,#3c5878,#5f7a96 40%,#d49a30 65%,#2a3550)}
.how-edge{position:absolute;left:605px;top:0;width:60px;height:537px;background:#fff;clip-path:polygon(80% 0,100% 0,22% 100%,0 100%)}
.how h2{position:absolute;left:112px;top:100px;font-size:46px;line-height:64px;color:#fff}
.how p{position:absolute;left:112px;top:262px;width:448px;font-size:16.5px;line-height:28px;color:#fff;text-align:justify}

/* cta */
.cta{position:absolute;left:0;top:3683px;width:1200px;height:505px;background:#fff;text-align:center}
.cta h2{position:absolute;left:0;width:1200px;top:140px;font-size:46px;line-height:64px}
.cta p{position:absolute;left:260px;width:680px;top:280px;font-size:16.5px;line-height:28px}
.chat{position:absolute;left:1082px;top:4135px;width:62px;height:62px;border-radius:50%;background:var(--orange-2);display:flex;align-items:center;justify-content:center;z-index:5}

/* footer */
.footer{position:absolute;left:0;top:4188px;width:1200px;height:507px;background:var(--navy);color:#fff}
.footer h3{font-family:"Oswald",sans-serif;font-weight:600;font-size:30px;text-transform:uppercase;position:absolute;top:95px}
.foot-about{position:absolute;left:141px;top:150px;width:309px;font-size:16.5px;line-height:28px;text-align:justify}
.contact-row{position:absolute;left:508px;display:flex;gap:16px;align-items:center;font-size:16.5px;line-height:28px}
.contact-icon{width:42px;height:42px;border-radius:50%;background:var(--orange);display:flex;align-items:center;justify-content:center;flex:none}
.links{position:absolute;left:832px;top:148px;list-style:none;font-size:15px;line-height:28px}
.links li{display:flex;gap:16px;align-items:center}
.links li::before{content:"»";color:var(--orange-2);font-weight:700}
.foot-bar{position:absolute;left:0;top:397px;width:1200px;height:1px;background:#2f2a52}
.social{position:absolute;top:432px;width:30px;height:30px;border-radius:50%;border:1px solid #6a6790}
.copy{position:absolute;left:0;width:1200px;top:438px;text-align:center;font-size:17px}
</style>
</head>
<body>

<header class="site-header">
  <div class="brand"><div class="brand-mark"></div><div class="brand-name">TARNOVEX</div></div>
  <div class="search">Search<div class="search-btn"></div></div>
  <div class="lang"><div class="lang-flag"></div>Eng ▾</div>
  <div class="mail">
    <svg width="14" height="11" viewBox="0 0 14 11"><rect x=".5" y=".5" width="13" height="10" fill="none" stroke="#fff"/><path d="M.5 .5 7 6 13.5 .5" fill="none" stroke="#fff"/></svg>
    Mail Us Today: <span>contacto@tarnovex.org</span>
  </div>
  <nav class="nav">
    <span class="active">Home</span><span>Industry Insights</span><span>Oil &amp; Gas Opportunities</span><span>Supplier &amp; Company Network</span><span>Register</span><span>News</span><span>Legal Framework</span>
  </nav>
</header>

<section class="hero" role="img" aria-label="Engineer in hard hat and orange jacket working on a laptop at a refinery at dusk">
  <div class="hero-worker"></div>
  <div class="hero-eyebrow">Access Mozambique's</div>
  <h1 class="hero-title">Oil &amp; Gas Industry<br>Intelligence in One<br>Platform</h1>
  <div class="btn" style="left:91px;top:413px;width:163px">Register Now</div>
  <div class="hero-arrow" style="left:91px"><svg width="8" height="12" viewBox="0 0 8 12"><path d="M6 1 1 6l5 5" fill="none" stroke="#16112f" stroke-width="2"/></svg></div>
  <div class="hero-arrow" style="left:133px"><svg width="8" height="12" viewBox="0 0 8 12"><path d="M2 1l5 5-5 5" fill="none" stroke="#16112f" stroke-width="2"/></svg></div>
</section>

<section class="unique">
  <div class="rule" style="left:571px;top:112px"></div>
  <h2 class="display">Why Tarnovex is Unique</h2>
  <svg class="abs" style="left:372px;top:280px" width="150" height="30" viewBox="0 0 150 30"><path d="M4 26 Q75 -6 140 20" fill="none" stroke="#fff" stroke-dasharray="4 4"/><path d="M134 14l8 6-9 3" fill="#fff"/></svg>
  <svg class="abs" style="left:676px;top:280px" width="150" height="30" viewBox="0 0 150 30"><path d="M4 26 Q75 -6 140 20" fill="none" stroke="#fff" stroke-dasharray="4 4"/><path d="M134 14l8 6-9 3" fill="#fff"/></svg>
  <div class="step" style="left:161px">
    <div class="step-ring"><div class="step-num">01</div><div class="step-core">
      <svg width="52" height="52" viewBox="0 0 52 52" fill="none" stroke="#1b1838" stroke-width="2"><path d="M6 46V26l10 6v-6l10 6v-6l10 6V10h8v36z"/><path d="M22 38h4M30 38h4M12 38h4" stroke="#e0531d"/></svg>
    </div></div>
    <h3>Up-to-date Industry<br>Intelligence</h3>
    <p>Receive frequent updates about developments in Mozambique's Oil &amp; Gas sector.</p>
  </div>
  <div class="step" style="left:465px">
    <div class="step-ring"><div class="step-num">02</div><div class="step-core">
      <svg width="52" height="52" viewBox="0 0 52 52" fill="none" stroke="#1b1838" stroke-width="2"><circle cx="26" cy="22" r="14"/><path d="M19 22l5 5 9-9" stroke="#e0531d"/><path d="M18 34l-4 14 6-3 4 5 2-12M34 34l4 14-6-3-4 5"/></svg>
    </div></div>
    <h3>High-quality Curated<br>Information</h3>
    <p>Access carefully selected and synthesized information tailored to industry stakeholders.</p>
  </div>
  <div class="step" style="left:768px">
    <div class="step-ring"><div class="step-num">03</div><div class="step-core">
      <svg width="52" height="52" viewBox="0 0 52 52" fill="none" stroke="#1b1838" stroke-width="2"><circle cx="22" cy="24" r="14"/><path d="M22 15v9l6 4" stroke="#e0531d"/><circle cx="38" cy="38" r="8" stroke="#e0531d"/></svg>
    </div></div>
    <h3>Time-saving<br>Access</h3>
    <p>Avoid spending hours searching through scattered online sources with organized and accessible content in one platform.</p>
  </div>
</section>

<section class="about">
  <svg class="abs" style="left:124px;top:96px" width="110" height="110" viewBox="0 0 110 110"><g stroke="#bbb" stroke-width="4"><path d="M0 20 20 0M0 40 40 0M0 60 60 0M0 80 80 0M0 100 100 0"/></g></svg>
  <svg class="abs" style="left:470px;top:450px" width="110" height="110" viewBox="0 0 110 110"><g stroke="#e0531d" stroke-width="4"><path d="M10 110 110 10M30 110 110 30M50 110 110 50M70 110 110 70"/></g></svg>
  <div class="about-photo" role="img" aria-label="Offshore oil platform lit at dusk over the sea under a purple sky"></div>
  <div class="rule" style="left:607px;top:114px"></div>
  <h2 class="display">What is <span class="accent">Tarnovex?</span></h2>
  <div class="about-text">
    <p>Tarnovex is a unique online platform built to connect businesses, investors, suppliers, and professionals with valuable information about the Mozambican Oil &amp; Gas sector.</p>
    <p style="margin-top:28px">Through a secure digital paywall system, users gain access to organized, up-to-date, and carefully selected industry information that supports better decision-making, market understanding, and business opportunities within Mozambique's growing hydrocarbons industry.</p>
  </div>
  <div class="btn" style="left:607px;top:500px;width:163px">Learn More <svg viewBox="0 0 9 12"><path d="M2 1l5 5-5 5" fill="none" stroke="#fff" stroke-width="2.4"/></svg></div>
</section>

<section class="access">
  <div class="rule" style="left:571px;top:107px"></div>
  <h2 class="display">What You <span class="accent">Will Access</span></h2>
  <div class="grid">
    <div class="cell">
      <svg viewBox="0 0 84 84" fill="none" stroke="#1b1838" stroke-width="2.4"><path d="M30 30h24l-4 10H34zM36 40l-8 38M48 40l8 38M32 56h20M30 68h24"/><path d="M20 8c-6 8-8 12-8 16a8 8 0 0016 0c0-4-2-8-8-16zM64 8c-6 8-8 12-8 16a8 8 0 0016 0c0-4-2-8-8-16z" stroke="#e0531d"/></svg>
      <h3>Hydrocarbon Industry<br>Information</h3>
      <p>General information and insights about Mozambique's oil and gas sector.</p>
    </div>
    <div class="cell featured">
      <svg viewBox="0 0 84 84" fill="none" stroke="#fff" stroke-width="2.4"><path d="M10 20l40-10 14 16M24 16l6 60M48 12l-6 64M22 76h44M30 44h14M28 60h18"/><path d="M64 26v20M58 46h12"/></svg>
      <h3>Main Gas<br>Projects</h3>
      <p>Details about major gas and energy projects operating in Mozambique.</p>
    </div>
    <div class="cell">
      <svg viewBox="0 0 84 84" fill="none" stroke="#1b1838" stroke-width="2.4"><ellipse cx="32" cy="16" rx="22" ry="8"/><path d="M10 16v40c0 4 10 8 22 8M54 16v16M10 30c0 4 10 8 22 8M10 44c0 4 10 8 22 8"/><circle cx="58" cy="58" r="12" stroke="#e0531d"/><circle cx="58" cy="58" r="5" stroke="#e0531d"/></svg>
      <h3>Supplier &amp; Company<br>Database</h3>
      <p>Mozambican companies capable of meeting Level 3 supply requirements.</p>
    </div>
    <div class="cell">
      <svg viewBox="0 0 84 84" fill="none" stroke="#1b1838" stroke-width="2.4"><path d="M12 76V40h16v36M28 76V30h20v46M48 76V44h20v32M8 76h68"/><path d="M18 30V10l-4 4M18 10l4 4M58 36V16" stroke="#e0531d"/></svg>
      <h3>Industry<br>Contacts</h3>
      <p>Key contacts from NOCs, Operators, EPCs, and Second-Tier Suppliers.</p>
    </div>
    <div class="cell">
      <svg viewBox="0 0 84 84" fill="none" stroke="#1b1838" stroke-width="2.4"><path d="M24 8h36v40H24z"/><path d="M32 18h20M32 26h20M32 34h12" stroke="#e0531d"/><path d="M8 60l14-10 16 6 10-4 20 8-14 14-18-4-12 4"/></svg>
      <h3>Tender<br>Opportunities</h3>
      <p>Short, medium, and long-term tenders within the industry.</p>
    </div>
    <div class="cell">
      <svg viewBox="0 0 84 84" fill="none" stroke="#1b1838" stroke-width="2.4"><circle cx="54" cy="30" r="18"/><path d="M54 12v18h18" stroke="#e0531d"/><path d="M8 64l14-8 20 4 14-6M8 76l18-4 22 4 26-14"/><path d="M20 44V20l-5 5M20 20l5 5" stroke="#e0531d"/></svg>
      <h3>Ownership &amp;<br>Access</h3>
      <p>Information related to hydrocarbon reserves and sector participation.</p>
    </div>
  </div>
  <div class="btn" style="left:519px;top:891px;width:162px">View More <svg viewBox="0 0 9 12"><path d="M2 1l5 5-5 5" fill="none" stroke="#fff" stroke-width="2.4"/></svg></div>
</section>

<section class="how">
  <div class="how-photo" role="img" aria-label="Bearded engineer in hard hat and hi-vis vest using a laptop at an industrial plant"></div>
  <div class="how-edge"></div>
  <div class="rule" style="left:112px;top:80px"></div>
  <h2 class="display">How the Platform<br>Works</h2>
  <p>The platform operates through a secure automated payment system that grants registered users access to premium and exclusive content. By subscribing, users receive organized industry intelligence designed to save time, improve market access, and support strategic business growth within Mozambique's energy sector.</p>
</section>

<section class="cta">
  <div class="rule" style="left:571px;top:110px"></div>
  <h2 class="display">Start Exploring Mozambique's<br><span class="accent">Oil &amp; Gas Opportunities</span></h2>
  <p>Register today to access premium industry information, supplier networks, tenders, and strategic market insights through Tarnovex.</p>
  <div class="btn" style="left:431px;top:352px;width:162px">Register Now <svg viewBox="0 0 9 12"><path d="M2 1l5 5-5 5" fill="none" stroke="#fff" stroke-width="2.4"/></svg></div>
  <div class="btn" style="left:607px;top:352px;width:162px">Contact Us</div>
</section>

<div class="chat"><svg width="26" height="22" viewBox="0 0 26 22"><path d="M3 3h20v13H10l-5 4v-4H3z" fill="none" stroke="#16112f" stroke-width="2"/></svg></div>

<footer class="footer">
  <h3 style="left:141px">About Us</h3>
  <p class="foot-about">Tarnovex is a modern online consulting platform designed to facilitate access to the Mozambican Oil and Gas industry through premium industry insights, supplier information, tenders, legal frameworks, and strategic project data.</p>
  <h3 style="left:508px">Contact Us</h3>
  <div class="contact-row" style="top:150px"><div class="contact-icon"><svg width="14" height="18" viewBox="0 0 14 18"><path d="M7 17s6-6 6-10A6 6 0 001 7c0 4 6 10 6 10z" fill="#16112f"/><circle cx="7" cy="7" r="2" fill="#e0531d"/></svg></div><span>12 Kestrel Lane<br>Marula Park, Vaalbrook South Africa</span></div>
  <div class="contact-row" style="top:224px"><div class="contact-icon"><svg width="16" height="12" viewBox="0 0 16 12"><rect x="1" y="1" width="14" height="10" fill="#16112f"/><path d="M1 1l7 6 7-6" fill="none" stroke="#e0531d"/></svg></div><span>contacto@tarnovex.org</span></div>
  <div class="contact-row" style="top:280px"><div class="contact-icon"><svg width="16" height="16" viewBox="0 0 16 16"><path d="M3 1l3 3-2 2c1 3 3 5 6 6l2-2 3 3-2 2C7 15 1 9 1 3z" fill="#16112f"/></svg></div><span>+1 555 014 2290</span></div>
  <h3 style="left:832px">Quick Links</h3>
  <ul class="links">
    <li>Home</li><li>Industry Insights</li><li>Oil &amp; Gas Opportunities</li><li>Supplier &amp; Company Network</li><li>Register</li><li>News</li><li>Legal Framework</li>
  </ul>
  <div class="foot-bar"></div>
  <div class="social" style="left:144px;background:#fff;border:none"></div>
  <div class="social" style="left:186px"></div>
  <div class="social" style="left:226px"></div>
  <div class="copy">© Copyrights 2026 | All Rights Reserved</div>
</footer>

</body>
</html>
```